Im open to ideas.. I was thinking on my business cards aswell as my logo. a place for my name. email. phone number and abn..

ive attched a file with my business logo. which i dont love the colours.. i was think a dark background with charcoal letters so something along those colour schumes but im open to ideas..

BRM Constructions

```html
<!DOCTYPE html>
<html lang="en">
<head>
<meta charset="UTF-8">
<title>BRM Constructions – Business Card</title>
<link rel="stylesheet" href="https://fonts.googleapis.com/css2?family=Open+Sans:wght@400;600;700&display=swap">
<style>
  :root {
    --backdrop: #3a3330;
    --card: #1b1b1c;
    --card-edge: #2a2a2b;
    --white: #f4f4f4;
    --grey: #a9a9a9;
    --muted: #4a4a4b;
    --red: #e2161d;
  }
  * { box-sizing: border-box; margin: 0; padding: 0; }
  html, body {
    width: 1200px; height: 787px; overflow: hidden;
    background: var(--backdrop);
    font-family: "Open Sans", Arial, sans-serif;
  }
  .canvas { position: relative; width: 1200px; height: 787px; }
  .card {
    position: absolute; top: 236px;
    width: 550px; height: 314px;
    background: var(--card);
    border: 1px solid var(--card-edge);
    border-radius: 4px;
  }
  .card--back { left: 35px; }
  .card--front { left: 615px; }

  /* back face */
  .back-name {
    position: absolute; left: 0; right: 0; top: 118px;
    text-align: center;
    font-weight: 700; font-size: 36px; letter-spacing: 3px;
    color: var(--muted); text-transform: uppercase;
  }
  .back-web {
    position: absolute; left: 44px; bottom: 44px;
    font-size: 13px; letter-spacing: 5px; color: var(--grey);
  }

  /* front face */
  .wordmark {
    position: absolute; right: 40px; top: 74px;
    font-weight: 700; font-size: 40px; letter-spacing: 2px;
    color: var(--white); text-transform: uppercase; line-height: 1;
  }
  .contact {
    position: absolute; left: 40px; bottom: 44px;
    display: flex; align-items: stretch;
  }
  .person { text-align: right; padding-right: 18px; padding-top: 2px; }
  .person__name { color: var(--red); font-size: 19px; line-height: 1.25; }
  .person__role { color: var(--white); font-size: 17px; line-height: 1.3; }
  .divider { width: 1px; background: var(--grey); margin-right: 18px; }
  .details { list-style: none; color: var(--white); font-size: 15px; }
  .details li { display: flex; align-items: center; gap: 10px; line-height: 1.75; }
  .details .icon { width: 15px; height: 15px; fill: var(--red); flex: none; }
  .details .spacer { width: 15px; flex: none; }
</style>
</head>
<body>
<main class="canvas">
  <section class="card card--back" aria-label="Card back">
    <p class="back-name">BRM Constructions</p>
    <p class="back-web">www.brmbuild.com</p>
  </section>

  <section class="card card--front" aria-label="Card front">
    <p class="wordmark">BRM Constructions</p>
    <div class="contact">
      <div class="person">
        <p class="person__name">Sam Carter</p>
        <p class="person__role">President</p>
      </div>
      <span class="divider"></span>
      <ul class="details">
        <li><span class="spacer"></span>ABN: 123456789</li>
        <li>
          <svg class="icon" viewBox="0 0 16 16" aria-hidden="true">
            <path d="M2 5c0-2 2-3 6-3s6 1 6 3v1h-3V5H5v1H2z"/>
            <path d="M4 7h8l2 6H2z"/>
          </svg>
          555 0142 7780
        </li>
        <li>
          <svg class="icon" viewBox="0 0 16 16" aria-hidden="true">
            <path d="M1 3h14v1L8 9 1 4z"/>
            <path d="M1 6l7 5 7-5v7H1z"/>
          </svg>
          sam@brmbuild.com
        </li>
      </ul>
    </div>
  </section>
</main>
</body>
</html>
```